Postcard Design

The business Logo is 'Borlow' it is grass cutting and maintenance. It will offer grass cutting with stripes including edging. Other services include decking/fencing maintenance, lawn treatment and patio/drive cleaning...... prices start from £10 to include front and rear lawns, Regular cuts or a one off tidy. private and commercial. Contracts welcome.
call 01632960418 or 07700900582 for a free quote.
one of the pics that i have sent is the logo (obviously it would need to be tidied up and neater) that is just rough. The other pic is one of nerro cards templates but is the one that is the preferred out of all of them. If it could be similar to that with the logo on would be great.
a before (long scruffy grass) and after (neat Lawn) half and half of the postcard would be great.

Target Market(s)

Middle class home owners.

Industry/Entity Type

Business

Requirements
Must have
• The 'Borlow' logo
Nice to have
• we have a lot of junk mail posted in this area and a lot just gets put in the bin so could you make it eye catching.

```html
<!DOCTYPE html>
<html lang="en">
<head>
<meta charset="utf-8">
<title>Borlow Lawn Care and Maintenance – Postcard</title>
<link href="https://fonts.googleapis.com/css2?family=Oswald:wght@300;400;600&display=swap" rel="stylesheet">
<style>
  :root {
    --bg: #2b2b2b;
    --ink: #111;
    --white: #fff;
    --grass-light: #7fbf3f;
    --grass-mid: #4f9a2a;
    --strip: #1f5a22;
    --brand: #1fa33a;
    --brand-bright: #3fd15a;
    --brand-deep: #0f6b25;
    --logo-ink: #16321a;
    --garden: #5f8f3a;
    --paving: #8a5a4a;
  }
  * { box-sizing: border-box; margin: 0; padding: 0; }
  html, body { width: 777px; height: 1200px; overflow: hidden; }
  body { background: var(--bg); font-family: "Oswald", sans-serif; font-weight: 300; position: relative; }

  .card { position: absolute; left: 21px; width: 734px; overflow: hidden; box-shadow: 0 4px 10px rgba(0,0,0,.6); }
  .card--front { top: 24px; height: 566px; }
  .card--back { top: 613px; height: 558px; }

  .photo { position: absolute; }
  .hero { left: 0; top: 0; width: 734px; height: 203px;
    background: linear-gradient(180deg, #3f6e2a 0%, #6b9a3a 50%, var(--grass-light) 66%, var(--grass-mid) 100%); }
  .gallery-strip { position: absolute; left: 0; top: 203px; width: 734px; height: 159px;
    background: linear-gradient(180deg, var(--strip), #2b7a2e 50%, var(--strip)); }
  .thumb { top: 15px; width: 229px; height: 131px; border: 3px solid var(--white); }
  .thumb--mowing { left: 11px; background: linear-gradient(160deg, #5fa53a, #d35a3a 45%, #6aa83a 70%); }
  .thumb--garden { left: 253px; background: linear-gradient(180deg, #c8d8e0 0%, var(--garden) 30%, #3f7a2a 75%, #6fb04a 100%); }
  .thumb--patio  { left: 494px; background: linear-gradient(170deg, #b8a890 0%, var(--paving) 55%, #6b3f35 100%); }
  .lawn-close { left: 0; top: 362px; width: 734px; height: 204px;
    background: linear-gradient(90deg, #5f9a38, #8cc25a 50%, #5a9436); }

  .brand { position: absolute; display: flex; flex-direction: column; align-items: flex-start; }
  .brand__name { display: flex; align-items: center; gap: 10px; color: var(--logo-ink); font-weight: 600; text-transform: uppercase; line-height: 1; }
  .brand__mark { display: inline-block; background: var(--logo-ink); }
  .brand__tag { color: var(--logo-ink); font-weight: 400; }
  .card--front .brand { left: 14px; top: 30px; }
  .card--front .brand__name { font-size: 62px; }
  .card--front .brand__mark { width: 22px; height: 22px; }
  .card--front .brand__tag { font-size: 15px; color: var(--white); margin-top: 4px; }

  .price-ribbon { position: absolute; left: 620px; top: 0; width: 90px; height: 139px;
    background: var(--brand); color: var(--white); text-align: center; padding-top: 11px;
    clip-path: polygon(0 0, 100% 0, 100% 100%, 50% 86%, 0 100%); }
  .price-ribbon__lead { font-size: 10px; display: block; }
  .price-ribbon__amount { font-size: 26px; font-weight: 600; display: block; line-height: 1.1; }
  .price-ribbon__note { font-size: 9.5px; display: block; line-height: 1.35; padding: 0 6px; }

  .quote-pill { position: absolute; left: 0; top: 473px; width: 372px; height: 73px;
    background: #151515; border-radius: 0 37px 37px 0; color: var(--white); text-align: center; padding-top: 7px; }
  .quote-pill__lead { font-size: 18px; display: block; line-height: 1.2; }
  .quote-pill__numbers { display: block; white-space: nowrap; font-size: 29px; color: var(--brand-bright); line-height: 1.2; }
  .or { font-size: 15px; color: var(--white); margin: 0 6px; }

  .before-after { left: 0; top: 0; width: 734px; height: 172px;
    background: linear-gradient(90deg, #4f8a2f 0%, #76b04a 49%, #84c25c 51%, #6aa842 100%); }
  .before-after__labels { position: absolute; left: 0; top: 143px; width: 734px; height: 29px;
    background: rgba(20,60,20,.45); display: flex; }
  .before-after__labels span { flex: 1; text-align: center; color: var(--white); font-size: 18px; letter-spacing: 1px; line-height: 29px; }

  .panel { position: absolute; left: 0; top: 172px; width: 734px; height: 338px;
    background: linear-gradient(180deg, var(--brand-deep) 0%, var(--brand) 35%, var(--brand-bright) 60%, var(--brand) 80%, var(--brand-deep) 100%); }
  .card--back .brand { left: 50px; top: 62px; }
  .card--back .brand__name { font-size: 74px; }
  .card--back .brand__mark { width: 26px; height: 26px; }
  .card--back .brand__tag { font-size: 22px; margin-top: 4px; }

  .quote-block { position: absolute; left: 16px; top: 234px; width: 350px; text-align: center; color: var(--ink); }
  .quote-block__lead { font-size: 19px; display: block; line-height: 1.3; }
  .quote-block__numbers { display: block; white-space: nowrap; font-size: 30px; line-height: 1.2; font-weight: 400; }
  .quote-block .or { color: var(--ink); }

  .services { position: absolute; left: 397px; top: 28px; width: 313px; height: 283px;
    background: #111; color: var(--white); text-align: center; padding-top: 20px;
    box-shadow: 0 4px 8px rgba(0,0,0,.5); }
  .services__title { font-size: 34px; font-weight: 300; letter-spacing: 2px; margin-bottom: 14px; }
  .services__list { list-style: none; font-size: 17px; line-height: 1.5; }
  .services__list li { margin-bottom: 7px; }

  .footer-bar { position: absolute; left: 0; top: 510px; width: 734px; height: 48px; background: #141414;
    color: var(--white); font-size: 23px; text-align: center; line-height: 46px;
    border-bottom: 4px solid var(--brand); }
</style>
</head>
<body>

<section class="card card--front">
  <div class="photo hero" role="img" aria-label="Striped lawn in front of a flower garden"></div>
  <div class="brand">
    <div class="brand__name"><span class="brand__mark"></span>Borlow</div>
    <div class="brand__tag">Lawn Care and Maintenance</div>
  </div>
  <div class="price-ribbon">
    <span class="price-ribbon__lead">start from</span>
    <span class="price-ribbon__amount">£10</span>
    <span class="price-ribbon__note">include front and rear lawns, regular cuts or a one off tidy</span>
  </div>
  <div class="gallery-strip">
    <div class="photo thumb thumb--mowing" role="img" aria-label="Lawn mower cutting grass"></div>
    <div class="photo thumb thumb--garden" role="img" aria-label="Well kept garden borders"></div>
    <div class="photo thumb thumb--patio" role="img" aria-label="Patio being pressure cleaned"></div>
  </div>
  <div class="photo lawn-close" role="img" aria-label="Close-up of freshly cut lawn"></div>
  <div class="quote-pill">
    <span class="quote-pill__lead">CALL TODAY FOR A FREE QUOTE</span>
    <span class="quote-pill__numbers">01632960418<span class="or">OR</span>07700900582</span>
  </div>
</section>

<section class="card card--back">
  <div class="photo before-after" role="img" aria-label="Long scruffy grass beside a neat cut lawn">
    <div class="before-after__labels"><span>BEFORE</span><span>AFTER</span></div>
  </div>
  <div class="panel">
    <div class="brand">
      <div class="brand__name"><span class="brand__mark"></span>Borlow</div>
      <div class="brand__tag">Lawn Care and Maintenance</div>
    </div>
    <div class="quote-block">
      <span class="quote-block__lead">CALL TODAY FOR A FREE QUOTE</span>
      <span class="quote-block__numbers">01632960418<span class="or">OR</span>07700900582</span>
    </div>
    <div class="services">
      <h2 class="services__title">OUR SERVICE</h2>
      <ul class="services__list">
        <li>Lawn cutting including edging, with stripes.<br>One Off or Regular Cuts</li>
        <li>Garden Maintenance and Lawn Treatment</li>
        <li>Hedge Trimming</li>
        <li>Decking/Fence Maintenance</li>
        <li>Patio and Drive Cleaning</li>
      </ul>
    </div>
  </div>
  <div class="footer-bar">Private, Commercial and Contracts Welcome</div>
</section>

</body>
</html>
```